Carpentry framing business card and logo design

We need a logo that works well with baseball caps, tee shirts and sweat shirts. We are a carpentry framing company specializing in apartment complexes and large residential communities. We work in what is known as the tri state area southeastern Pennsylvania , New Jersey and northern Delaware . We would like to see die signs using the old English letter M and royal blue colors. Also we stress OSHA compliance and safety.

Industry/Entity Type

Residential

Contact Information for Business Card

Valdrick Construction Co Inc
4870 Quillford Lane
Brellmont OH 44871
Dale Valdrick
dale1valdrick@norvexmail.com
555-815-0926

```html
<!DOCTYPE html>
<html lang="en">
<head>
<meta charset="utf-8">
<title>Valdrick Construction Co Inc – Business Card</title>
<link rel="stylesheet" href="https://fonts.googleapis.com/css2?family=Arimo:wght@400;700&display=swap">
<style>
  :root {
    --bg: #e9e9e6;
    --card-white: #fbfbf9;
    --card-black: #111213;
    --green: #6cc94f;
    --ink: #1b1b1b;
    --text-light: #f2f2f2;
  }
  * { box-sizing: border-box; margin: 0; padding: 0; }
  html, body { width: 1200px; height: 818px; overflow: hidden; }
  body {
    background: var(--bg);
    font-family: "Arimo", Arial, sans-serif;
    position: relative;
  }
  .card {
    position: absolute;
    top: 259px;
    width: 525px;
    height: 300px;
    overflow: hidden;
    box-shadow: 0 6px 18px rgba(0,0,0,0.18);
  }
  .card-front { left: 50px; background: var(--card-white); }
  .card-back  { left: 625px; background: var(--card-black); }
  .card-shapes { position: absolute; inset: 0; width: 100%; height: 100%; }

  .brand {
    position: absolute;
    left: 44px;
    top: 100px;
    width: 320px;
  }
  .brand-rule { height: 3px; background: var(--green); width: 250px; margin-left: 40px; }
  .brand-row { display: flex; align-items: center; gap: 14px; margin: 16px 0; }
  .brand-square { width: 32px; height: 32px; background: var(--green); flex: none; }
  .brand-name {
    font-weight: 400;
    font-size: 17px;
    line-height: 1.3;
    letter-spacing: 1.5px;
    color: var(--ink);
    text-transform: uppercase;
    white-space: nowrap;
  }
  .brand-rule-thin { height: 2px; background: var(--green); width: 270px; margin-left: 20px; }

  .contact {
    position: absolute;
    right: 28px;
    top: 58px;
    text-align: right;
  }
  .contact-name {
    color: var(--green);
    font-weight: 700;
    font-size: 27px;
    margin-bottom: 18px;
    padding-right: 30px;
    white-space: nowrap;
  }
  .contact-line {
    display: flex;
    justify-content: flex-end;
    align-items: center;
    gap: 12px;
    color: var(--text-light);
    font-size: 16px;
    margin-bottom: 11px;
    white-space: nowrap;
  }
  .contact-icon { width: 18px; height: 18px; flex: none; }
</style>
</head>
<body>
  <section class="card card-front" aria-label="Business card front">
    <svg class="card-shapes" viewBox="0 0 525 300" aria-hidden="true">
      <path d="M318 0 Q448 150 392 300 L422 300 Q478 150 360 0 Z" fill="var(--green)"/>
      <path d="M360 0 Q478 150 422 300 L525 300 L525 0 Z" fill="var(--card-black)"/>
    </svg>
    <div class="brand">
      <div class="brand-rule"></div>
      <div class="brand-row">
        <span class="brand-square"></span>
        <span class="brand-name">Valdrick<br>Construction Co Inc</span>
      </div>
      <div class="brand-rule-thin"></div>
    </div>
  </section>

  <section class="card card-back" aria-label="Business card back">
    <svg class="card-shapes" viewBox="0 0 525 300" aria-hidden="true">
      <path d="M0 0 L120 0 Q30 150 80 300 L0 300 Z" fill="var(--card-white)"/>
      <path d="M120 0 Q30 150 80 300 L118 300 Q70 150 165 0 Z" fill="var(--green)"/>
    </svg>
    <div class="contact">
      <div class="contact-name">Dale Valdrick</div>
      <div class="contact-line">
        <span>555-815-0926</span>
        <svg class="contact-icon" viewBox="0 0 18 18" aria-hidden="true">
          <circle cx="9" cy="6" r="4" fill="var(--green)"/>
          <path d="M2 17 Q9 7 16 17 Z" fill="var(--green)"/>
        </svg>
      </div>
      <div class="contact-line">
        <span>dale1valdrick@norvexmail.com</span>
        <svg class="contact-icon" viewBox="0 0 18 18" aria-hidden="true">
          <rect x="1" y="3" width="16" height="12" rx="1.5" fill="var(--green)"/>
          <path d="M1.5 4 L9 10 L16.5 4" stroke="var(--card-black)" stroke-width="1.4" fill="none"/>
        </svg>
      </div>
      <div class="contact-line">
        <span>4870 Quillford Lane Brellmont OH 44871</span>
        <svg class="contact-icon" viewBox="0 0 18 18" aria-hidden="true">
          <path d="M9 1 C5 1 3 4 3 7 C3 11 9 17 9 17 C9 17 15 11 15 7 C15 4 13 1 9 1 Z" fill="var(--green)"/>
          <circle cx="9" cy="7" r="2.2" fill="var(--card-black)"/>
        </svg>
      </div>
    </div>
  </section>
</body>
</html>
```